"The Plumewright" nails, eyelash extensions and hair extensions. Need an eye catching design for bu

Need an eye catching design focusing on eyelash extensions, nail extensions and hair extensions. I like the colour green, black, glitter, pink?! need the design to be innovative and 'POP'. I'd like more emphasis on lashes and nails.
I'd like the business name and my phone number on the front of card.
Would really like something different and unique.
"The Plumewright"
Nails, Eyelash & Hair Extensions
Mira
0471526093

Target Market(s)

20-40

Industry/Entity Type

Beauty Salon

Contact Information for Business Card

Id like my business name, My name and phone number on the front of card
"The Plumewright".
Mira.
0471526093.
Id like some catchy design involving long lashes with possibly glitter, long hair and nails. Id like the lashes to be the first thing you see at first glance. I'm open to your creative flair. Just need the business card design to 'POP'! I like the colours green, black, pink, silver or gold glitter. wether it's pop art, 3d drawn pictures, isolated pics of lash, nails or hair, card design could be in black and white with isolated colours added..i'm open to your creative flair. use a font which stands out and easy to read.
(The back of the card will be used for writing appointment times.)

Font styles to use
Serif

Colors
6b449b
e667a6
25b39d

Requirements
Must have
• Long lashes, hair, nails.
• one sided
Nice to have
• bright catchy colours, innovative, uniqueness

```html
<!DOCTYPE html>
<html lang="en">
<head>
<meta charset="utf-8">
<title>The Plumewright — Business Card</title>
<link rel="stylesheet" href="https://fonts.googleapis.com/css2?family=Fira+Sans:wght@400;500;600&display=swap">
<style>
  :root {
    --canvas-bg: #e9e7e4;
    --card-white: #ffffff;
    --brand-purple: #7552a6;
    --brand-pink: #e2579f;
    --photo-black: #111111;
    --photo-dark: #2a2a2a;
    --photo-mid: #777777;
    --photo-light: #c9c9c9;
    --text-light: #ffffff;
    --card-shadow: 0 10px 24px rgba(0, 0, 0, 0.18);
  }
  * { box-sizing: border-box; margin: 0; padding: 0; }
  html, body {
    width: 1200px;
    height: 900px;
    overflow: hidden;
    background: var(--canvas-bg);
    font-family: "Fira Sans", Arial, sans-serif;
  }
  .canvas {
    width: 1200px;
    height: 900px;
    display: flex;
    align-items: center;
    justify-content: center;
    gap: 40px;
  }
  .card {
    width: 540px;
    height: 309px;
    box-shadow: var(--card-shadow);
    position: relative;
    overflow: hidden;
  }
  .card-back {
    background:
      radial-gradient(ellipse 45% 55% at 42% 48%, var(--photo-light) 0%, var(--photo-mid) 45%, transparent 100%),
      radial-gradient(ellipse 30% 40% at 85% 20%, var(--photo-mid) 0%, transparent 100%),
      linear-gradient(100deg, var(--photo-black) 0%, var(--photo-dark) 55%, var(--photo-mid) 100%);
  }
  .card-front {
    background: var(--card-white);
  }
  .brand-area {
    position: absolute;
    top: 0; left: 0; right: 0;
    height: 133px;
    display: flex;
    align-items: center;
    padding-left: 66px;
    gap: 40px;
  }
  .brand-dot {
    width: 30px;
    height: 30px;
    border-radius: 50%;
    background: var(--brand-pink);
    flex: none;
  }
  .brand-name {
    font-size: 36px;
    font-weight: 500;
    color: var(--brand-purple);
    letter-spacing: 0.3px;
    line-height: 1;
  }
  .divider {
    position: absolute;
    top: 133px; left: 0; right: 0;
    height: 3px;
    background: var(--brand-pink);
  }
  .info-band {
    position: absolute;
    top: 142px; left: 0; right: 0; bottom: 0;
    background: var(--brand-purple);
    color: var(--text-light);
    text-align: center;
  }
  .person-name {
    margin-top: 16px;
    font-size: 22px;
    font-weight: 600;
    line-height: 1.2;
  }
  .phone {
    margin-top: 4px;
    font-size: 19px;
    font-weight: 400;
    line-height: 1.2;
    display: flex;
    align-items: center;
    justify-content: center;
    gap: 6px;
  }
  .phone svg { width: 15px; height: 15px; }
  .services {
    position: absolute;
    left: 0; right: 0;
    bottom: 34px;
    font-size: 17px;
    font-weight: 600;
    line-height: 1.2;
  }
</style>
</head>
<body>
  <main class="canvas">
    <section class="card card-back" role="img" aria-label="Black and white beauty photograph: a woman with long flowing hair, long extended eyelashes and manicured nails, lying back holding a vintage telephone receiver"></section>

    <section class="card card-front">
      <div class="brand-area">
        <span class="brand-dot"></span>
        <span class="brand-name">The Plumewright</span>
      </div>
      <div class="divider"></div>
      <div class="info-band">
        <p class="person-name">Mira</p>
        <p class="phone">
          <svg viewBox="0 0 24 24" aria-hidden="true"><path fill="#ffffff" d="M6.6 10.8a15.1 15.1 0 0 0 6.6 6.6l2.2-2.2a1 1 0 0 1 1-.25 11.4 11.4 0 0 0 3.6.57 1 1 0 0 1 1 1V20a1 1 0 0 1-1 1A17 17 0 0 1 3 4a1 1 0 0 1 1-1h3.5a1 1 0 0 1 1 1c0 1.25.2 2.45.57 3.57a1 1 0 0 1-.25 1z"/></svg>
          0471526093
        </p>
        <p class="services">Nails, Eyelash Extensions and Hair Extensions</p>
      </div>
    </section>
  </main>
</body>
</html>
```